Business Cards for IT Consulting Company (Managed Service Provider)

I am looking to have some business cards printed and would like some designs. We are an IT Consulting company based in Vancouver BC. I would like a nice clean and modern look to the cards. I have uploaded all the versions of my logo so parts can be used as needed. Here is a snippit from our website homepage:

Quillbrook Networks Ltd. is an IT Solutions Partner located in Vancouver BC, Canada. We offer IT solutions and support to customers in the greater Vancouver Area. With expertise in Microsoft platforms, as well as Linux and Mac OSX and over 12 years experience in the IT industry, Quillbrook Networks is dedicated to offering our clients top quality service and products. We take pride in the solutions we offer our customers. The greatest compliment a client can give us is to recommend our services.

Quillbrook Networks Ltd. offers a wide range of IT services from onsite service to remote support and managed service solutions. This allows clients to choose the support path that best suits their company’s needs. Supporting many different sized companies from small to enterprise level over the past 12 years Quillbrook Networks has the experience and expertise needed to ensure things run smoothly. Allowing our clients to focus on doing business.

Revolutionizing the way IT services are delivered.

Quillbrook Networks is dedicated to providing our clients with IT solutions that work and grow with them for years to come. This philosophy helps save money in the long run instead of replacing equipment constantly. Far too often IT solutions are not well thought out and while possibly solving the problem at hand, require replacement due to growth or quality within a very short time frame. Quillbrook Networks takes pride in providing solutions that will last and be able to accommodate growth without the need for replacement.

Industry/Entity Type

Information Technology

Contact Information for Business Card

Quillbrook Networks Ltd.
(Employee Name)
Eml: (Employees Email Address)
Web: quillbrook.me
Ph: 604-555-0148

Font styles to use
Serif
Sans Serif

Requirements
Must have
• The Company logo and company colors.
Nice to have
• - Our tag line: "Revolutionizing IT Services" or "Revolutionizing the way IT services are delivered."
• - Also I really like the idea of nature and technology together blending which is sort of where my logo came from so integrating that somehow onto the business cards would be great.

```html
<!DOCTYPE html>
<html lang="en">
<head>
<meta charset="utf-8">
<title>Quillbrook Networks Ltd. — Business Cards</title>
<link href="https://fonts.googleapis.com/css2?family=Roboto:ital,wght@0,400;0,500;1,400&display=swap" rel="stylesheet">
<style>
  :root {
    --backdrop: #a8a6a7;
    --card: #f7f7f7;
    --brand-blue: #1a8ad4;
    --ink: #444447;
    --ink-soft: #5a5a5e;
    --band-grey: #4a4a4d;
    --rule: #6d6d70;
  }
  * { margin: 0; padding: 0; box-sizing: border-box; }
  html, body { width: 1200px; height: 1200px; overflow: hidden; }
  body {
    background: var(--backdrop);
    font-family: "Roboto", Arial, sans-serif;
    color: var(--ink);
    position: relative;
  }
  .card {
    position: absolute;
    width: 712px;
    background: var(--card);
    overflow: hidden;
  }
  .card--front { left: 238px; top: 118px; height: 419px; }
  .card--back  { left: 231px; top: 645px; height: 416px; }

  .wordmark {
    position: absolute;
    display: flex;
    align-items: center;
    gap: 18px;
    color: var(--brand-blue);
    font-weight: 500;
  }
  .wordmark__square {
    width: 54px; height: 54px;
    background: var(--brand-blue);
    flex: none;
  }
  .wordmark__text { display: flex; flex-direction: column; line-height: 1; }
  .wordmark__name { font-size: 76px; letter-spacing: -1px; }
  .wordmark__suffix { font-size: 22px; letter-spacing: 1.5px; margin-top: 4px; margin-left: 4px; }

  .card--front .wordmark { left: 110px; top: 132px; }
  .card--back .wordmark { left: 38px; top: 52px; }
  .card--back .wordmark__name { font-size: 72px; }
  .card--back .wordmark__suffix { font-size: 21px; }

  .front-tagline {
    position: absolute;
    left: 100px; right: 100px; top: 376px;
    display: flex; align-items: center; gap: 16px;
    font-size: 18px; color: var(--ink-soft); white-space: nowrap;
  }
  .front-tagline__rule { flex: 1; height: 3px; background: var(--brand-blue); }
  .front-tagline__rule--left { background: linear-gradient(to right, transparent, var(--brand-blue) 40%); }
  .front-tagline__rule--right { background: linear-gradient(to left, transparent, var(--brand-blue) 40%); }

  .person { position: absolute; right: 35px; top: 196px; text-align: right; }
  .person__name { font-size: 25px; font-weight: 500; color: var(--brand-blue); }
  .person__title { font-size: 16px; font-style: italic; color: var(--ink); margin-top: 6px; }

  .divider { position: absolute; left: 37px; top: 245px; width: 482px; height: 1px; background: var(--rule); }

  .contacts { position: absolute; left: 38px; top: 276px; list-style: none; }
  .contacts li {
    display: flex; align-items: center; gap: 16px;
    font-size: 18px; color: var(--ink); height: 27px;
  }
  .contacts svg { width: 18px; height: 18px; fill: var(--brand-blue); flex: none; }

  .back-tagline {
    position: absolute; right: 35px; top: 298px;
    text-align: right; font-size: 18px; line-height: 26px; color: var(--ink);
  }

  .band-grey { position: absolute; left: 0; bottom: 0; width: 360px; height: 21px; background: var(--band-grey); }
  .band-blue { position: absolute; right: 0; bottom: 0; width: 386px; height: 49px; }
</style>
</head>
<body>

<section class="card card--front" aria-label="Card front">
  <div class="wordmark">
    <span class="wordmark__square"></span>
    <span class="wordmark__text">
      <span class="wordmark__name">quillbrook</span>
      <span class="wordmark__suffix">NETWORKS LTD.</span>
    </span>
  </div>
  <div class="front-tagline">
    <span class="front-tagline__rule front-tagline__rule--left"></span>
    <span>Revolutionizing IT Services</span>
    <span class="front-tagline__rule front-tagline__rule--right"></span>
  </div>
</section>

<section class="card card--back" aria-label="Card back">
  <div class="wordmark">
    <span class="wordmark__square"></span>
    <span class="wordmark__text">
      <span class="wordmark__name">quillbrook</span>
      <span class="wordmark__suffix">NETWORKS LTD.</span>
    </span>
  </div>

  <div class="person">
    <div class="person__name">Marcus Ellery</div>
    <div class="person__title">Managing Director</div>
  </div>

  <div class="divider"></div>

  <ul class="contacts">
    <li>
      <svg viewBox="0 0 20 20" aria-hidden="true"><path d="M2 6c0-2 3-3 8-3s8 1 8 3v2h-4V6.5c-1-.5-2.5-.7-4-.7s-3 .2-4 .7V8H2z"/><path d="M5 9h10l2 8H3z M8 11v2h4v-2z"/></svg>
      <span>604-555-0148</span>
    </li>
    <li>
      <svg viewBox="0 0 20 20" aria-hidden="true"><path d="M10 1a9 9 0 1 0 0 18 9 9 0 0 0 0-18zm0 2c1 0 2 2.3 2.3 6H7.7C8 5.3 9 3 10 3zM3.1 9a7 7 0 0 1 3.6-5.2C6 5.3 5.7 7 5.6 9zm0 2h2.5c.1 2 .4 3.7 1.1 5.2A7 7 0 0 1 3.1 11zM10 17c-1 0-2-2.3-2.3-6h4.6C12 14.7 11 17 10 17zm3.3-.8c.7-1.5 1-3.2 1.1-5.2h2.5a7 7 0 0 1-3.6 5.2zM14.4 9c-.1-2-.4-3.7-1.1-5.2A7 7 0 0 1 16.9 9z"/></svg>
      <span>www.quillbrook.me</span>
    </li>
    <li>
      <svg viewBox="0 0 20 20" aria-hidden="true"><path d="M1 4h18v12H1z M3 6v.3l7 5 7-5V6z M3 8.6V14h14V8.6l-7 5z" fill-rule="evenodd"/></svg>
      <span>support@quillbrook.me</span>
    </li>
  </ul>

  <p class="back-tagline">Revolutionizing the way<br>IT services are delivered</p>

  <div class="band-grey"></div>
  <svg class="band-blue" viewBox="0 0 386 49" preserveAspectRatio="none" aria-hidden="true">
    <polygon points="0,49 32,0 386,0 386,49" fill="var(--brand-blue)"/>
  </svg>
</section>

</body>
</html>
```